Detail Shop Business card design

i need a business card design for my new detailing company called 'Brisk's Polish Works'. i want an all black and white design . simple, direct and to the point. i want the designer to choose a fitting font to match the logothe front should have logo, address, phone and email and the back side should have a slogan and text indicating that we offer services on anything including cars, trucks, motorcycles and RVs. slogan will read "we take pride in your ride"
maybe also very small on the back side the IG icon with Brisks_Polish_Works

phone 208.417.6352
address 3847 E Larkin Ave
Spokane WA 99214
email: BrisksPolish@mailvexo.com

Target Market(s)

all ages , auto enthusiasts

Industry/Entity Type

Automotive

Contact Information for Business Card

the front should have logo, address, phone and email and the back side should have a slogan and text indicating that we offer services on anything including cars, trucks, motorcycles and RVs. slogan will read "we take pride in your ride"

phone 208.417.6352
address 3847 E Larkin Ave
Spokane WA 99214

Colors
000000
ffffff

Requirements
Must have
• bold font and very simple design with good spacing
Nice to have
• anything creative from the designer indicating we service any types of vehicles
Should not have
• any colors ,

```html
<!DOCTYPE html>
<html lang="en">
<head>
<meta charset="utf-8">
<title>Brisk's Polish Works – Business Card</title>
<link href="https://fonts.googleapis.com/css2?family=Lato:wght@400;700;900&display=swap" rel="stylesheet">
<style>
  :root {
    --ink: #000000;
    --paper: #ffffff;
    --stage: #2b2b2d;
    --card-w: 600px;
    --card-h: 343px;
  }
  * { margin: 0; padding: 0; box-sizing: border-box; }
  html, body { width: 1200px; height: 800px; overflow: hidden; }
  body {
    background: var(--stage);
    font-family: "Lato", Arial, sans-serif;
    position: relative;
  }
  .card {
    position: absolute;
    width: var(--card-w);
    height: var(--card-h);
    overflow: hidden;
    box-shadow: 0 18px 40px rgba(0,0,0,0.45);
  }
  .card--back { left: 80px; top: 50px; background: var(--ink); color: var(--paper); }
  .card--front { left: 520px; top: 407px; background: var(--paper); color: var(--ink); }

  .card__shapes { position: absolute; inset: 0; width: 100%; height: 100%; }

  .brand {
    position: absolute;
    display: flex;
    align-items: center;
    gap: 12px;
    font-weight: 900;
    font-size: 30px;
    letter-spacing: 0.5px;
    line-height: 1;
    white-space: nowrap;
  }
  .brand__dot { width: 22px; height: 22px; border-radius: 50%; }
  .card--back .brand { left: 50%; top: 92px; transform: translateX(-50%); color: var(--paper); }
  .card--back .brand__dot { background: var(--paper); }
  .card--front .brand { left: 50%; top: 120px; transform: translateX(-50%); color: var(--ink); }
  .card--front .brand__dot { background: var(--ink); }

  .slogan {
    position: absolute;
    left: 0; right: 0;
    top: 262px;
    text-align: center;
    font-weight: 700;
    font-size: 17px;
    letter-spacing: 5px;
    color: var(--paper);
  }

  .contact {
    position: absolute;
    display: flex;
    align-items: center;
    gap: 10px;
    color: var(--paper);
    font-size: 16px;
    white-space: nowrap;
  }
  .contact svg { width: 16px; height: 16px; flex: none; }
  .contact--phone { left: 26px; top: 251px; }
  .contact--email { right: 26px; top: 251px; }
  .contact--address { left: 26px; top: 297px; font-size: 15px; }
</style>
</head>
<body>

  <section class="card card--back" aria-label="Card back">
    <svg class="card__shapes" viewBox="0 0 600 343" aria-hidden="true">
      <polygon points="0,196 260,196 270,206 330,206 340,196 600,196 590,212 600,228 340,228 330,218 270,218 260,228 0,228 10,212" fill="#ffffff"/>
      <rect x="286" y="198" width="28" height="28" fill="#000000" stroke="#ffffff" stroke-width="3"/>
    </svg>
    <div class="brand"><span class="brand__dot"></span><span>Brisk's Polish Works</span></div>
    <p class="slogan">we take pride in your ride</p>
  </section>

  <section class="card card--front" aria-label="Card front">
    <svg class="card__shapes" viewBox="0 0 600 343" aria-hidden="true">
      <polygon points="0,240 250,240 268,260 250,280 0,280" fill="#000000"/>
      <polygon points="600,240 330,240 312,260 330,280 600,280" fill="#000000"/>
      <rect x="0" y="286" width="600" height="42" fill="#000000"/>
      <rect x="0" y="334" width="600" height="9" fill="#000000"/>
    </svg>
    <div class="brand"><span class="brand__dot"></span><span>Brisk's Polish Works</span></div>

    <div class="contact contact--phone">
      <svg viewBox="0 0 16 16" aria-hidden="true"><path d="M3 1h3l1.5 4-2 1.2a9 9 0 0 0 4.3 4.3L11 8.5l4 1.5v3c0 1-1 2-2 2A12 12 0 0 1 1 3c0-1 1-2 2-2z" fill="#ffffff"/></svg>
      <span>208.417.6352</span>
    </div>
    <div class="contact contact--email">
      <svg viewBox="0 0 16 16" aria-hidden="true"><rect x="1" y="3" width="14" height="10" fill="#ffffff"/><path d="M1 3l7 6 7-6" fill="none" stroke="#000000" stroke-width="1.4"/></svg>
      <span>BrisksPolish@mailvexo.com</span>
    </div>
    <div class="contact contact--address">
      <span>3847 E Larkin Ave, Spokane WA 99214</span>
    </div>
  </section>

</body>
</html>
```